Dental office stationary (letterhead, envelopes), business cards, presentation folders

Nothing too dental outside of the logo. I will need all stationary, presentation folders, business cards. Would prefer to stay in the colors of the logo

Gordon Patel, DDS
Bright Haven Dental Implant Center
555-318-2790
info@brighthavendental.example
4817 NW Maple Crest Rd Unit B
Stuart, FL 00000

Also need appointment date and time
And cancellation policy
I want it to say “kindly ask for
A 48hr cancellation policy to avoid incurring a cancellation fee”

Industry/Entity Type

Dental

Colors
0054AA
0677BA
7BADD7
CADEEF
E8F1F8

Requirements
Must have
• Name of your office, name of doctor, address, phone number
Should not have
• Too much tooth/dental. Only the tooth in logo

```html
<!DOCTYPE html>
<html lang="en">
<head>
<meta charset="utf-8">
<title>Bright Haven Dental Implant Center – Business Card</title>
<link rel="stylesheet" href="https://fonts.googleapis.com/css2?family=Roboto:wght@400;500;700&display=swap">
<style>
  :root {
    --canvas: #2a2c30;
    --card-white: #ffffff;
    --brand-blue: #0b67b5;
    --brand-blue-deep: #0054aa;
    --brand-sky: #17c0ee;
    --brand-teal: #17b898;
    --text-dark: #3a3d42;
    --divider: #8a8d92;
    --emboss: #0a5aa0;
  }
  * { box-sizing: border-box; margin: 0; padding: 0; }
  html, body { width: 1200px; height: 900px; overflow: hidden; }
  body {
    background: var(--canvas);
    font-family: "Roboto", Arial, sans-serif;
    display: flex;
    flex-direction: column;
    align-items: center;
    justify-content: center;
    gap: 40px;
  }
  .card {
    position: relative;
    width: 700px;
    height: 400px;
    overflow: hidden;
    box-shadow: 0 10px 30px rgba(0,0,0,.45);
  }
  .card-front { background: var(--card-white); }
  .card-back { background: var(--brand-blue); display: flex; align-items: center; justify-content: center; }

  .front-wave { position: absolute; inset: 0; width: 100%; height: 100%; }

  .brand-name {
    position: absolute;
    left: 50px;
    top: 92px;
    width: 300px;
    display: flex;
    align-items: center;
    gap: 10px;
    font-weight: 500;
    font-size: 30px;
    letter-spacing: 1px;
    color: var(--brand-teal);
    text-transform: uppercase;
    line-height: 1;
    white-space: nowrap;
  }
  .brand-dot {
    width: 18px; height: 18px; border-radius: 50%;
    background: var(--brand-blue);
    flex: none;
  }
  .divider {
    position: absolute;
    left: 370px; top: 70px;
    width: 1.5px; height: 230px;
    background: var(--divider);
  }
  .contact {
    position: absolute;
    left: 392px; top: 74px;
    width: 290px;
    color: var(--text-dark);
    font-size: 15px;
    line-height: 1.45;
  }
  .contact-name { font-weight: 700; font-size: 21px; color: var(--brand-blue); margin-bottom: 2px; }
  .contact-office { font-size: 16px; margin-bottom: 10px; }
  .contact-address { margin-bottom: 14px; }
  .contact-line { display: flex; align-items: center; gap: 7px; }
  .contact-line svg { width: 14px; height: 14px; flex: none; }
  .web-domain { color: var(--brand-teal); }

  .back-name {
    font-weight: 500;
    font-size: 64px;
    letter-spacing: 4px;
    color: var(--emboss);
    text-transform: uppercase;
  }
</style>
</head>
<body>
  <section class="card card-front" aria-label="Business card front">
    <svg class="front-wave" viewBox="0 0 700 400" preserveAspectRatio="none" aria-hidden="true">
      <defs>
        <linearGradient id="bandGradient" x1="0" y1="0" x2="1" y2="0.4">
          <stop offset="0" stop-color="#17c0ee"/>
          <stop offset="0.6" stop-color="#0e86cf"/>
          <stop offset="1" stop-color="#0b67b5"/>
        </linearGradient>
      </defs>
      <path d="M0 190 C 50 300, 260 330, 470 350 C 560 358, 610 372, 630 400 L0 400 Z" fill="url(#bandGradient)"/>
      <path d="M0 150 C 30 250, 200 300, 440 336 C 250 318, 60 290, 22 165 Z" fill="var(--brand-teal)"/>
    </svg>

    <div class="brand-name"><span class="brand-dot"></span>Bright Haven</div>

    <div class="divider"></div>

    <div class="contact">
      <p class="contact-name">Gordon Patel, DDS</p>
      <p class="contact-office">Bright Haven Dental Implant Center</p>
      <p class="contact-address">4817 NW Maple Crest Rd Unit B<br>Stuart, FL 00000</p>
      <p class="contact-line">
        <svg viewBox="0 0 16 16" aria-hidden="true"><path fill="#17b898" d="M3 2h3l1 3-2 1a8 8 0 0 0 5 5l1-2 3 1v3a1 1 0 0 1-1 1A12 12 0 0 1 2 3a1 1 0 0 1 1-1z"/></svg>
        555-318-2790
      </p>
      <p class="contact-line">
        <svg viewBox="0 0 16 16" aria-hidden="true"><rect x="1" y="3" width="14" height="10" rx="1.5" fill="#17b898"/><path d="M1.5 4 8 9l6.5-5" stroke="#fff" stroke-width="1.4" fill="none"/></svg>
        info@brighthavendental.example
      </p>
      <p class="contact-line">
        <svg viewBox="0 0 16 16" aria-hidden="true"><circle cx="8" cy="8" r="7" fill="#17b898"/><path d="M1 8h14M8 1c3 3 3 11 0 14M8 1c-3 3-3 11 0 14" stroke="#fff" stroke-width="1" fill="none"/></svg>
        <span>www.<span class="web-domain">brighthavendental</span>.example</span>
      </p>
    </div>
  </section>

  <section class="card card-back" aria-label="Business card back">
    <p class="back-name">Bright Haven</p>
  </section>
</body>
</html>
```